business card deign

Logo needs the following on it.
1. attached logo
2. Tagline - "Cold drinks, loud speakers, long nights...we bring it all!"
3. Name- Dalton Pikes, Founder and CPO
4. Address - 412 E. Carver Avenue, Ste 2207, Tampa, FL. 33917
5. Phone - 555.318.4726

```html
<!DOCTYPE html>
<html lang="en">
<head>
<meta charset="utf-8">
<title>Brisco Business Card</title>
<link rel="stylesheet" href="https://fonts.googleapis.com/css2?family=Montserrat:wght@300;400;700&display=swap">
<style>
  :root {
    --page: #141414;
    --card: #262626;
    --ink: #ffffff;
    --ink-soft: #e6e6e6;
    --pattern-dark: #1e1e1e;
    --pattern-light: #4a4a4a;
  }
  * { box-sizing: border-box; margin: 0; padding: 0; }
  html, body {
    width: 1200px;
    height: 900px;
    overflow: hidden;
    background: var(--page);
    font-family: "Montserrat", sans-serif;
    color: var(--ink);
  }
  .sheet {
    width: 1200px;
    height: 900px;
    display: flex;
    flex-direction: column;
    align-items: center;
    justify-content: center;
    gap: 60px;
  }
  .card {
    position: relative;
    width: 620px;
    height: 354px;
    border-radius: 22px;
    background: var(--card);
    overflow: hidden;
    box-shadow: 0 14px 30px rgba(0,0,0,0.55);
  }

  /* Front */
  .holder {
    position: absolute;
    left: 44px;
    top: 48px;
  }
  .holder-name {
    font-weight: 700;
    font-size: 25px;
    letter-spacing: 0.5px;
    text-transform: uppercase;
    line-height: 1.1;
  }
  .holder-role {
    font-weight: 300;
    font-size: 17px;
    margin-top: 2px;
    color: var(--ink-soft);
  }
  .divider {
    position: absolute;
    left: 44px;
    right: 44px;
    top: 196px;
    height: 1px;
    background: var(--ink);
  }
  .contact {
    position: absolute;
    left: 44px;
    top: 214px;
    list-style: none;
    font-size: 16px;
    font-weight: 400;
    line-height: 1.55;
  }
  .contact li { display: flex; align-items: center; gap: 8px; }
  .contact svg { width: 14px; height: 14px; fill: var(--ink); flex: none; }
  .address {
    position: absolute;
    right: 44px;
    bottom: 34px;
    text-align: right;
    font-size: 16px;
    font-weight: 400;
    font-style: normal;
    line-height: 1.4;
  }
  .brand {
    display: flex;
    align-items: center;
    gap: 10px;
    font-weight: 700;
    text-transform: uppercase;
    letter-spacing: 10px;
    color: var(--ink);
  }
  .brand-dot {
    width: 14px;
    height: 14px;
    border-radius: 50%;
    background: var(--ink);
    flex: none;
  }
  .front .brand {
    position: absolute;
    right: 44px;
    top: 120px;
    font-size: 30px;
  }

  /* Back */
  .back-pattern {
    position: absolute;
    inset: 0;
    background: linear-gradient(115deg, var(--pattern-dark) 0%, #2c2c2c 45%, var(--pattern-light) 100%);
  }
  .back-content {
    position: absolute;
    inset: 0;
    display: flex;
    flex-direction: column;
    align-items: center;
    justify-content: center;
    gap: 26px;
  }
  .back .brand { font-size: 34px; }
  .tagline {
    font-size: 17px;
    font-weight: 400;
  }
</style>
</head>
<body>
<main class="sheet">
  <section class="card front" aria-label="Card front">
    <div class="holder">
      <h1 class="holder-name">Dalton Pikes</h1>
      <p class="holder-role">Founder and CPO</p>
    </div>
    <div class="brand"><span class="brand-dot"></span>Brisco</div>
    <div class="divider"></div>
    <ul class="contact">
      <li>
        <svg viewBox="0 0 16 16" aria-hidden="true"><path d="M3.6 1.2l2.3 2.6c.4.4.4 1 0 1.4L4.8 6.4a9 9 0 0 0 4.8 4.8l1.2-1.1c.4-.4 1-.4 1.4 0l2.6 2.3c.4.4.4 1 0 1.4l-1.3 1.3c-.7.7-1.8.9-2.7.5A15 15 0 0 1 .6 5.4C.2 4.5.4 3.4 1.1 2.7L2.2 1.2c.4-.4 1-.4 1.4 0z"/></svg>
        555.318.4726
      </li>
      <li>
        <svg viewBox="0 0 16 16" aria-hidden="true"><path d="M1 3h14v10H1z M2 4.2v.4l6 4 6-4v-.4z" fill-rule="evenodd"/></svg>
        daltonpikes@brisco-mail.com
      </li>
    </ul>
    <address class="address">
      412 E. Carver Avenue<br>
      Ste 2207, Tampa, FL. 33917
    </address>
  </section>

  <section class="card back" aria-label="Card back">
    <div class="back-pattern" role="img" aria-label="Repeating brand pattern in dark grey tones"></div>
    <div class="back-content">
      <div class="brand"><span class="brand-dot"></span>Brisco</div>
      <p class="tagline">Cold drinks, loud speakers, long nights...we bring it all!</p>
    </div>
  </section>
</main>
</body>
</html>
```